Request for Business Card Design

Hi. My name is Marlene, I am looking for a new business card design for my company, Quarrow Signal Instruments, LLC. I really like the design you did for Tarsel Venture and was hoping you could do something similar using our full logo and our mark. I am also open to any raised texture design using our mark. I have attached our full logo, which would need to be somewhere on the card, as well as the mark in both outline and full form, as well as our brand colors / guide. The card does not have to be white, as long as our logo and mark appear. I actually like darker colored business cards more, but am open to all options. If you are interested in working with me, please let me know. We would also take the business card design into letterhead design if you can do that.

```html
<!DOCTYPE html>
<html lang="en">
<head>
<meta charset="utf-8">
<title>Quarrow Signal Instruments – Business Card</title>
<link href="https://fonts.googleapis.com/css2?family=Open+Sans:wght@400;600;700&display=swap" rel="stylesheet">
<style>
  :root {
    --stage: #222223;
    --card: #3a3a3c;
    --card-dark: #2b2b2d;
    --ink: #f2f2f2;
    --ink-soft: #d8d8d8;
    --brand-blue: #1d9bc6;
    --silver: #9a9a9c;
  }
  * { box-sizing: border-box; margin: 0; padding: 0; }
  html, body {
    width: 1200px; height: 780px; overflow: hidden;
    background: var(--stage);
    font-family: "Open Sans", Arial, sans-serif;
    color: var(--ink);
  }
  .card-set {
    position: absolute; top: 235px; left: 50px;
    display: flex; gap: 40px;
  }
  .card {
    position: relative; width: 530px; height: 303px;
    background: var(--card); overflow: hidden;
    box-shadow: 0 14px 30px rgba(0,0,0,.45);
  }

  /* Brand lockup */
  .brand {
    position: absolute; display: flex; align-items: center; gap: 10px;
  }
  .brand__dot {
    width: 34px; height: 34px; border-radius: 50%;
    background: var(--brand-blue); flex: none;
  }
  .brand__name {
    font-weight: 700; font-size: 19px; letter-spacing: .06em;
    text-transform: uppercase; color: var(--ink); line-height: 1.15;
  }
  .card--front .brand { top: 26px; left: 28px; }

  /* Contact block */
  .contact { position: absolute; top: 92px; left: 28px; }
  .contact__name {
    font-weight: 700; font-size: 32px; color: var(--brand-blue); line-height: 1.05;
  }
  .contact__role { font-size: 14px; color: var(--ink-soft); margin-bottom: 8px; }
  .contact__address { font-size: 13px; line-height: 1.4; color: var(--ink); margin-bottom: 8px; }
  .contact__lines { list-style: none; font-size: 13px; line-height: 1.55; }
  .contact__lines li { display: flex; align-items: center; gap: 8px; }
  .contact__icon { width: 12px; height: 12px; flex: none; }
  .contact__icon * { fill: none; stroke: var(--brand-blue); stroke-width: 1.6; }

  .raised-texture {
    position: absolute; right: -20px; bottom: -30px;
    width: 290px; height: 270px;
    background: radial-gradient(circle at 55% 50%, #505052 0%, #2a2a2c 45%, #3a3a3c 72%);
    border-radius: 50%;
  }

  /* Back */
  .card--back { background: var(--card-dark); }
  .pattern-field {
    position: absolute; inset: 0;
    background: linear-gradient(110deg, #2a2a2c 0%, #333335 45%, #6a6a6c 80%, var(--silver) 100%);
  }
  .card--back .brand { right: 28px; bottom: 24px; }
  .card--back .brand__dot { width: 22px; height: 22px; }
  .card--back .brand__name { font-size: 14px; }
</style>
</head>
<body>
  <main class="card-set">
    <section class="card card--front" aria-label="Card front">
      <div class="brand">
        <span class="brand__dot"></span>
        <span class="brand__name">Quarrow Signal<br>Instruments</span>
      </div>

      <div class="contact">
        <p class="contact__name">Marlene</p>
        <p class="contact__role">Director</p>
        <p class="contact__address">118 Fenwick Mill Road •<br>Harlow Ridge, CO 80921</p>
        <ul class="contact__lines">
          <li>
            <svg class="contact__icon" viewBox="0 0 12 12"><path d="M3 1 L5 3.5 L4 5 Q5.5 7 7 8 L8.5 7 L11 9 L9.5 11 Q4 10 1 3 Z"/></svg>
            +001 555 210 4417
          </li>
          <li>
            <svg class="contact__icon" viewBox="0 0 12 12"><rect x="1" y="5" width="10" height="6"/><rect x="3" y="1" width="6" height="4"/></svg>
            +001 555 210 4418
          </li>
          <li>
            <svg class="contact__icon" viewBox="0 0 12 12"><circle cx="6" cy="6" r="5"/><path d="M1 6 H11 M6 1 Q3 6 6 11 Q9 6 6 1"/></svg>
            www.quarrowsignal.com
          </li>
          <li>
            <svg class="contact__icon" viewBox="0 0 12 12"><rect x="1" y="2.5" width="10" height="7"/><path d="M1 2.5 L6 7 L11 2.5"/></svg>
            info@quarrowsignal.com
          </li>
        </ul>
      </div>

      <div class="raised-texture" role="img" aria-label="Large raised brand mark texture"></div>
    </section>

    <section class="card card--back" aria-label="Card back">
      <div class="pattern-field" role="img" aria-label="Repeating brand mark pattern fading from dark grey to silver"></div>
      <div class="brand">
        <span class="brand__dot"></span>
        <span class="brand__name">Quarrow Signal Instruments</span>
      </div>
    </section>
  </main>
</body>
</html>
```